Local Chiropractor Needs Up Scale Webdesign

This website needs to have an upscale look with a very modern feel. Below is the information and websites to reference

Add Logo that is attached

Build a color scheme similar to this website image titled "chiro-1"

Must Include these pages in a horizontal menu bar in this order:
Home, Meet Our Staff, Patient Testimonials, Videos, Work Place Wellness, Contact

Build a "classy looking" Make An Appointment Button into the header with the contact info below

Phone Number:
555-314-2719

Address:
3168 Pelham Orchard Lane, #240
Larkfield, MN 55990

This website needs 4 rotating banners. Please reference a layout similar to this for the banners: http://drmorlatz.example/. However design it nicer than this website, this website is very boring and doesn't flow with the colors properly

Below are the description for each banner

Rotating Banner #1
Use Image: Pediatrics
Two lines of text. First line title line, second description. Use Latin text for fill

Rotating Banner #2
Use Image: Aging Gracefully

Rotating Banner #3
Use Image: Pregnancy

Rotating Banner #4
Use Image: Athletics

I'd like to see a free consultation box similar to the "chiro-1" image. Fields to include are: First Name, Last Name, Phone Number, Comments.

For the body, please fill it with latin text. Please design a professional body layout. You can include a box in the right column for the hours

Office Hours
Monday: 8:00-11:00, 2:00-5:00
Tuesday: 8:30-11:00, 2:00-5:30
Wednesday: 8:00-11:00, 2:00-5:00
Thursday: 10:00-12:00, 2:30-5:00
Friday: 8:00-10:00, 1:00-5:00
Saturday: Closed
Sunday: Closed

For the footer please design something similar to the: http://drmorlatz.example/

Also include in the Footer: Powered by Brightline Site Works

```html
<!DOCTYPE html>
<html lang="en">
<head>
<meta charset="utf-8">
<title>Evergreen Vitality Chiropractic Health Center</title>
<link href="https://fonts.googleapis.com/css2?family=Dosis:wght@300;400;500;600;700&family=Open+Sans:wght@400;700&family=Oswald:wght@300;400&display=swap" rel="stylesheet">
<style>
:root{
  --charcoal:#4a4a4a;
  --lime:#c5dc3a;
  --lime-deep:#aec321;
  --olive:#8aa01a;
  --green-text:#8fb31d;
  --ink:#555;
  --white:#fff;
  --black:#0c0c0c;
  --orange:#cf4f22;
  --cyan:#27c4cf;
}
*{margin:0;padding:0;box-sizing:border-box}
html,body{width:731px;height:1200px;overflow:hidden;background:#fff}
body{position:relative;font-family:"Dosis",sans-serif;color:var(--ink)}
.abs{position:absolute}

/* header */
.site-header{left:0;top:0;width:731px;height:65px;background:var(--charcoal)}
.brand{left:77px;top:18px;display:flex;align-items:center;gap:6px}
.brand-dot{width:22px;height:22px;border-radius:50%;background:var(--lime)}
.brand-name{font-size:17px;font-weight:500;color:var(--lime);line-height:1}
.address-tab{left:286px;top:0;width:218px;height:18px;background:#fff;clip-path:polygon(0 0,100% 0,97% 100%,3% 100%);display:flex;align-items:center;justify-content:center;gap:4px;font-size:9px;color:#444;white-space:nowrap}
.header-phone{left:338px;top:28px;display:flex;align-items:center;gap:6px;color:#fff;font-size:16px;font-weight:500}
.appt-btn{left:542px;top:13px;width:112px;height:34px;border:2px solid #fff;border-radius:17px;background:var(--lime);display:flex;align-items:center;gap:8px;padding-left:10px}
.appt-btn span{font-family:"Open Sans",sans-serif;font-style:italic;font-weight:700;font-size:8.5px;color:var(--charcoal);line-height:1.2;text-align:center}

/* nav */
.main-nav{left:0;top:65px;width:731px;height:27px;background:var(--lime)}
.main-nav a{position:absolute;top:0;height:27px;display:flex;align-items:center;justify-content:center;font-size:9.5px;color:#5a6a10;text-decoration:none;border-left:1px solid #9cb320}
.main-nav a.last{border-right:1px solid #9cb320}

/* hero */
.hero-photo{left:0;top:92px;width:731px;height:314px;background:linear-gradient(180deg,#e9ece1 0%,#b9c680 35%,#97ac44 70%,#a8b84c 100%)}
.hero-figure{left:370px;top:92px;width:300px;height:314px;background:linear-gradient(160deg,#f3eee6,#e8c6ad 60%,#efe6df);border-radius:140px 140px 0 0}
.hero-copy{left:72px;top:192px;width:322px;text-align:center;color:#fff}
.hero-copy h1{font-family:"Open Sans",sans-serif;font-size:16.5px;font-weight:700;margin-bottom:6px}
.hero-copy p{font-size:9.8px;font-weight:600;line-height:1.4}
.hero-btn{left:186px;top:255px;width:72px;height:23px;background:var(--charcoal);color:#fff;font-size:10px;font-weight:600;display:flex;align-items:center;justify-content:center}

/* welcome */
.welcome-mark{left:90px;top:428px;width:30px;height:30px;border-radius:50%;background:var(--lime)}
.welcome-title{left:160px;top:427px;font-size:23px;font-weight:300;color:var(--green-text)}
.welcome-sub{left:207px;top:456px;font-size:12px;color:#555}
.welcome-text{left:76px;top:494px;width:206px;font-size:8.2px;line-height:15.7px;color:#666;white-space:nowrap}
.welcome-text strong{display:block;color:var(--green-text);font-size:8.8px;font-weight:600}
.welcome-photo{left:284px;top:500px;width:177px;height:127px;background:linear-gradient(180deg,#b9b0a6,#d9d6d3 45%,#8c4d68)}
.consult{left:473px;top:429px;width:183px;height:201px;background:var(--lime)}
.consult-head{left:0;top:0;width:183px;height:54px;background:var(--charcoal);clip-path:polygon(0 0,100% 0,100% 70%,50% 100%,0 70%);text-align:center;padding-top:3px}
.consult-head .l1{font-size:9px;color:var(--lime)}
.consult-head .l2{font-family:"Oswald",sans-serif;font-size:12px;color:#fff;letter-spacing:.5px}
.consult-head .l3{font-size:9px;color:var(--lime)}
.consult-tag{left:0;top:57px;width:183px;text-align:center;font-size:11px;font-weight:600;color:#4b5a0a}
.field{left:20px;width:142px;height:15px;background:#fff;font-size:6.8px;color:#999;padding:4px 5px}
.submit{left:20px;top:174px;width:142px;height:14px;background:var(--olive);color:#fff;font-size:7.5px;font-weight:700;letter-spacing:1px;display:flex;align-items:center;justify-content:center}
.rule{left:0;top:648px;width:731px;height:1px;background:#ddd}

/* video & hours */
.video{left:76px;top:663px;width:385px;height:183px;background:linear-gradient(135deg,#3d4d2a,#7a8f4a 45%,#3b4a2c)}
.video-bar{left:76px;top:663px;width:385px;height:24px;background:rgba(0,0,0,.55);color:#fff;font-size:9.5px;display:flex;align-items:center;justify-content:space-between;padding:0 10px}
.play{left:259px;top:743px;width:46px;height:30px;border-radius:8px;background:#e52d27}
.hours{left:473px;top:663px;width:182px;height:183px;background:var(--charcoal)}
.hours h3{height:20px;text-align:center;font-family:"Oswald",sans-serif;font-weight:400;color:#fff;font-size:11px;padding-top:2px}
.hours li{list-style:none;margin:0 4px;height:22.4px;background:var(--lime);border-bottom:1px solid #a9bf28;font-size:7.6px;letter-spacing:.5px;color:#4b5a0a;display:flex;align-items:center;padding-left:4px}

/* testimonial */
.quote-band{left:0;top:863px;width:731px;height:134px;background:var(--lime-deep);border-top:2px solid #92a61a}
.quote-text{left:120px;top:910px;width:492px;text-align:center;font-size:10px;line-height:13.6px;color:#3f4a08;white-space:nowrap}
.quote-name{left:0;top:958px;width:731px;text-align:center;font-family:"Open Sans",sans-serif;font-style:italic;font-size:9.6px;color:#333;line-height:12px}

/* footer */
.footer{left:0;top:997px;width:731px;height:203px;background:var(--black)}
.tab-info{left:76px;top:997px;width:289px;height:32px;background:var(--orange);color:#fff;font-family:"Oswald",sans-serif;font-weight:300;font-size:15px;display:flex;align-items:center;justify-content:center}
.tab-news{left:367px;top:997px;width:288px;height:32px;background:var(--cyan);color:#fff;font-family:"Oswald",sans-serif;font-weight:300;font-size:15px;display:flex;align-items:center;justify-content:center}
.f-title{font-size:12px;color:#fff;border-bottom:1px solid #fff;padding-bottom:1px}
.f-item{left:76px;display:flex;align-items:center;gap:8px;color:#fff;font-size:8.8px;line-height:13px}
.map{left:252px;top:1051px;width:166px;height:98px;border:2px solid var(--lime-deep);background:linear-gradient(135deg,#e3e9d8,#cfe0c2 50%,#9fc3e6)}
.f-hours{left:455px;top:1054px;width:130px;font-size:7.3px;color:#fff}
.f-hours div{display:flex;height:15.6px;align-items:center;border-bottom:1px solid #777}
.f-hours span:first-child{width:53px}
</style>
</head>
<body>

<header class="abs site-header"></header>
<div class="abs brand"><span class="brand-dot"></span><span class="brand-name">Evergreen Vitality</span></div>
<div class="abs address-tab">
  <svg width="7" height="10" viewBox="0 0 10 14"><path d="M5 0C2.2 0 0 2.2 0 5c0 3.8 5 9 5 9s5-5.2 5-9c0-2.8-2.2-5-5-5z" fill="#8fb31d"/><circle cx="5" cy="5" r="2" fill="#fff"/></svg>
  3168 Pelham Orchard Lane, #240 Larkfield, MN 55990
</div>
<div class="abs header-phone">
  <svg width="16" height="16" viewBox="0 0 20 20"><circle cx="10" cy="10" r="9" fill="none" stroke="#fff" stroke-width="1.6"/><path d="M7 5l2 3-1.2 1.2c.7 1.4 1.6 2.3 3 3L12 11l3 2-1 2c-4 0-8-4-8-8z" fill="#fff"/></svg>
  555-314-2719
</div>
<div class="abs appt-btn">
  <svg width="18" height="16" viewBox="0 0 18 16"><rect x="1" y="3" width="16" height="12" fill="#333"/><rect x="4" y="1" width="2" height="4" fill="#333"/><rect x="12" y="1" width="2" height="4" fill="#333"/><g fill="#c5dc3a"><rect x="4" y="7" width="2" height="2"/><rect x="8" y="7" width="2" height="2"/><rect x="12" y="7" width="2" height="2"/><rect x="4" y="11" width="2" height="2"/><rect x="8" y="11" width="2" height="2"/></g></svg>
  <span>Make An<br>Appointment</span>
</div>

<nav class="abs main-nav">
  <a style="left:76px;width:69px">Home</a>
  <a style="left:145px;width:104px">Meet Our Staff</a>
  <a style="left:249px;width:123px">Patient Testimonials</a>
  <a style="left:372px;width:75px">Videos</a>
  <a style="left:447px;width:125px">Work Place Wellness</a>
  <a class="last" style="left:572px;width:83px">Contact</a>
</nav>

<div class="abs hero-photo" role="img" aria-label="Smiling mother holding her toddler in a sunny green meadow"></div>
<div class="abs hero-figure" role="img" aria-label="Mother and child figures"></div>
<div class="abs hero-copy">
  <h1>The standard Lorem Ipsum passage</h1>
  <p>Sed ut perspiciatis unde omnis iste natus error sit voluptatem accusantium doloremque laudantium, totam rem tore veritatis</p>
</div>
<div class="abs hero-btn">Know More</div>

<div class="abs welcome-mark"></div>
<div class="abs welcome-title">Welcome To Evergreen Vitality</div>
<div class="abs welcome-sub">Chiropractic health Center</div>
<div class="abs welcome-text"><strong>Sed ut perspiciatis unde omnis iste natus error sit</strong>voluptatem accusantium doloremque laudantium, totam rem<br>aperiam, eaque ipsa quae ab illo inventore veritatis et quasi<br>architecto beatae vitae dicta sunt explicabo. Nemo enim ipsam<br>voluptatem quia voluptas sit aspernatur aut odit aut fugit, sed<br>quia consequuntur magni dolores eos qui ratione voluptatem<br>sequi nesciunt. Neque porro quisquam est, qui dolorem ipsum<br>quia dolor sit amet, consectetur, adipisci velit, sed quia non<br>numquam eius modi tempora incidunt ut labore et dolore</div>
<div class="abs welcome-photo" role="img" aria-label="Hands forming a heart shape over flower petals"></div>

<section class="abs consult">
  <div class="abs consult-head"><div class="l1">Contact Us Now And Get Your</div><div class="l2">FREE CONSULTATION</div><div class="l3">— Today —</div></div>
  <div class="abs consult-tag">WELLNESS BEGINS HERE</div>
  <div class="abs field" style="top:77px">First Name</div>
  <div class="abs field" style="top:98px">Last Name</div>
  <div class="abs field" style="top:119px">Phone Number</div>
  <div class="abs field" style="top:140px;height:28px;padding-top:10px">Comment....</div>
  <div class="abs submit">SUBMIT</div>
</section>
<div class="abs rule"></div>

<div class="abs video" role="img" aria-label="Two women jogging along a forest trail"></div>
<div class="abs video-bar"><span>Lorem Ipsum is simply dummy text of the printing and typesetting</span>
  <svg width="14" height="14" viewBox="0 0 14 14"><circle cx="11" cy="3" r="2.2" fill="#fff"/><circle cx="3" cy="7" r="2.2" fill="#fff"/><circle cx="11" cy="11" r="2.2" fill="#fff"/><path d="M3 7L11 3M3 7l8 4" stroke="#fff" stroke-width="1.3"/></svg>
</div>
<div class="abs play"><svg width="46" height="30" viewBox="0 0 46 30"><path d="M19 9l10 6-10 6z" fill="#fff"/></svg></div>

<section class="abs hours">
  <h3>OFFICE HOURS</h3>
  <ul>
    <li>MONDAY: 8:00-11:00, 2:00-5:00</li>
    <li>TUESDAY: 8:30-11:00, 2:00-5:30</li>
    <li>WEDNESDAY: 8:00-11:00, 2:00-5:00</li>
    <li>THURSDAY: 10:00-12:00, 2:30-5:00</li>
    <li>FRIDAY: 8:00-10:00, 1:00-5:00</li>
    <li>SATURDAY: CLOSED</li>
    <li>SUNDAY: CLOSED</li>
  </ul>
</section>

<div class="abs quote-band"></div>
<svg class="abs" style="left:352px;top:877px" width="30" height="26" viewBox="0 0 30 26"><path d="M0 26V13C0 5 4 1 12 0v5c-4 1-5 3-5 7h5v14zM17 26V13c0-8 4-12 12-13v5c-4 1-5 3-5 7h5v14z" fill="#5c6a12"/></svg>
<p class="abs quote-text">Lorem ipsum dolor sit amet, couer adicing elit. Praesent vesean nauris. Pasellus porta. Fusce<br>suscipit vars mi. Cciis nque penatibus et magnis dis parturient montes, nascmus. Nulla dui. Fusce<br>feugiat malesuada odio i nunc odio, gravida at, cursus nec, luctus a, lorem.</p>
<div class="abs quote-name">Marla Quinn<br>usa</div>

<footer class="abs footer"></footer>
<div class="abs tab-info">BASIC INFORMATION</div>
<div class="abs tab-news">NEWS LATTERS</div>
<div class="abs" style="left:77px;top:1038px"><span class="f-title">CONTACT</span></div>
<div class="abs f-item" style="top:1060px">
  <svg width="14" height="22" viewBox="0 0 10 14"><path d="M5 0C2.2 0 0 2.2 0 5c0 3.8 5 9 5 9s5-5.2 5-9c0-2.8-2.2-5-5-5z" fill="#fff"/><circle cx="5" cy="5" r="2" fill="#000"/></svg>
  <span>3168 PELHAM ORCHARD LANE, #240<br>LARKFIELD, MN 55990</span>
</div>
<div class="abs f-item" style="top:1098px">
  <svg width="18" height="18" viewBox="0 0 20 20"><circle cx="10" cy="10" r="9" fill="none" stroke="#fff" stroke-width="1.6"/><path d="M7 5l2 3-1.2 1.2c.7 1.4 1.6 2.3 3 3L12 11l3 2-1 2c-4 0-8-4-8-8z" fill="#fff"/></svg>
  <span>555-314-2719</span>
</div>
<div class="abs f-item" style="top:1128px">
  <svg width="18" height="14" viewBox="0 0 18 14"><rect x="1" y="1" width="16" height="12" fill="none" stroke="#fff" stroke-width="1.4"/><path d="M1 1l8 7 8-7M1 13l6-5M17 13l-6-5" fill="none" stroke="#fff" stroke-width="1.2"/></svg>
  <span>hello@evergreenvitality.example</span>
</div>
<div class="abs map" role="img" aria-label="Street map of the clinic location with a marker"></div>
<div class="abs" style="left:456px;top:1036px"><span class="f-title" style="font-size:10px">OFFICE HOURS</span></div>
<div class="abs f-hours">
  <div><span>MONDAY:</span><span>8:00-11:00, &nbsp;2:00-5:00</span></div>
  <div><span>TUESDAY:</span><span>8:30-11:00, &nbsp;2:00-5:30</span></div>
  <div><span>WEDNESDAY:</span><span>8:00-11:00, &nbsp;2:00-5:00</span></div>
  <div><span>THURSDAY :</span><span>10:00-12:00, &nbsp;2:30-5:00</span></div>
  <div><span>FRIDAY:</span><span>8:00-10:00, &nbsp;1:00-5:00</span></div>
  <div><span>SATURDAY:</span><span>CLOSED</span></div>
  <div><span>SUNDAY:</span><span>CLOSED</span></div>
</div>

</body>
</html>
```